Building technology company seek stationery design and folder design

Letterhead, and a folder design
ideally, I would have two letter head design, one is for one-page bussiness letter. the other one I can use for longer document such report, or analysis regular report page
you can find company logo and overall style at our website:
www.structavolt.example

we are in building technology business, using internet of things technology to improve building energy efficiency to make building greener.

Industry/Entity Type

It Company

Requirements
Must have
• company logo
Nice to have
• techy look abstract graphics, etc.
Should not have
• no comment

```html
<!DOCTYPE html>
<html lang="en">
<head>
<meta charset="utf-8">
<title>StructaVolt Folder</title>
<link rel="stylesheet" href="https://fonts.googleapis.com/css2?family=Questrial&family=Open+Sans:wght@400&display=swap">
<style>
  :root {
    --stage: #c4c4c4;
    --back-cover: #0a1b1e;
    --back-cover-light: #0f2528;
    --skyline: #706e60;
    --front-cover: #ffffff;
    --brand-green: #8cbc2e;
    --band-text: #f2f7e6;
  }
  * { margin: 0; padding: 0; box-sizing: border-box; }
  html, body {
    width: 1200px;
    height: 1090px;
    overflow: hidden;
    background: var(--stage);
  }
  .folder {
    position: absolute;
    left: 80px;
    top: 190px;
    width: 1040px;
    height: 710px;
    display: flex;
    box-shadow: 0 18px 40px rgba(0, 0, 0, 0.25);
  }
  .back-cover {
    position: relative;
    width: 520px;
    height: 100%;
    background: linear-gradient(160deg, var(--back-cover-light), var(--back-cover) 60%);
  }
  .skyline {
    position: absolute;
    left: 0;
    bottom: 0;
    width: 100%;
    height: 150px;
    display: block;
  }
  .front-cover {
    position: relative;
    width: 520px;
    height: 100%;
    background: var(--front-cover);
  }
  .brand {
    position: absolute;
    top: 170px;
    left: 0;
    width: 100%;
    display: flex;
    align-items: center;
    justify-content: center;
    gap: 12px;
  }
  .brand-mark {
    width: 22px;
    height: 22px;
    background: var(--brand-green);
  }
  .brand-name {
    font-family: "Questrial", sans-serif;
    font-size: 30px;
    letter-spacing: 4px;
    color: var(--brand-green);
    text-transform: uppercase;
  }
  .web-band {
    position: absolute;
    right: 0;
    bottom: 40px;
    width: 200px;
    height: 24px;
    background: var(--brand-green);
    display: flex;
    align-items: center;
    justify-content: flex-end;
    padding-right: 14px;
  }
  .web-address {
    font-family: "Open Sans", sans-serif;
    font-size: 9px;
    color: var(--band-text);
  }
</style>
</head>
<body>
  <div class="folder">
    <section class="back-cover">
      <svg class="skyline" viewBox="0 0 520 150" role="img" aria-label="City skyline silhouette along the bottom of the back cover">
        <rect x="0" y="0" width="520" height="150" fill="var(--skyline)"/>
      </svg>
    </section>
    <section class="front-cover">
      <div class="brand">
        <span class="brand-mark"></span>
        <span class="brand-name">StructaVolt</span>
      </div>
      <div class="web-band">
        <span class="web-address">www.structavolt.example</span>
      </div>
    </section>
  </div>
</body>
</html>
```